UI/ UX Design for ERP Software

We need a new UX/UI interface for a ERP software for property managers. Our CMMS / ERP solution is made based on responsive design technologies and is coded in PHP.
The overall UX to be similar to Tev Ulna - easy navigation, intuitive menus.

Industry/Entity Type

Property Management

Number of Pages Required

5+ page

Requirements
Must have
• Round dock buttons
Consistent icons across the application
Enough Spacing between buttons/icons/ menu
Consistent Font
Nice to have
• We would like the UX to allow the users to use the application without /minimum training.
Should not have
• we don't want anything that is classic with respect to UX

```html
<!DOCTYPE html>
<html lang="en">
<head>
<meta charset="utf-8">
<title>Estavo – Active Dashboard</title>
<link href="https://fonts.googleapis.com/css2?family=Roboto:wght@400;500&display=swap" rel="stylesheet">
<style>
:root{
  --sidebar:#4f6078;
  --sidebar-line:#45556b;
  --header:#f3f7fb;
  --page:#f6f6f6;
  --accent:#14a8f7;
  --brand:#1a8fe3;
  --ink:#444b55;
  --muted:#666;
  --grid:#e3e3e3;
  --white:#fff;
}
*{box-sizing:border-box;margin:0;padding:0}
html,body{width:1200px;height:1160px;overflow:hidden}
body{font-family:"Roboto",sans-serif;background:var(--page);color:var(--ink);position:relative}
.brand{position:absolute;left:0;top:0;width:217px;height:82px;background:var(--header);border-right:1px solid #e2e6ea;display:flex;align-items:center;justify-content:center;gap:8px}
.brand-mark{width:14px;height:14px;background:var(--brand)}
.brand-name{font-size:26px;font-weight:500;color:var(--brand)}
.topbar{position:absolute;left:217px;top:0;right:0;height:82px;background:var(--header);border-bottom:1px solid #e2e6ea}
.page-title{position:absolute;left:18px;top:31px;font-size:17.5px;display:flex;align-items:center;gap:8px;color:#333}
.stat{position:absolute;top:24px;height:40px;text-align:center;font-size:10.5px;color:#555;text-transform:uppercase}
.stat b{display:flex;justify-content:center;align-items:center;gap:4px;font-weight:400;font-size:12.5px;color:#444;text-transform:none;margin-top:6px}
.stat-sep{position:absolute;top:24px;width:1px;height:40px;background:#cfd5db}
.sidebar{position:absolute;left:0;top:82px;width:217px;height:1078px;background:var(--sidebar);list-style:none}
.sidebar li{height:41.4px;border-bottom:1px solid var(--sidebar-line);display:flex;align-items:center;padding-left:20px;color:var(--white);font-size:12.5px;font-weight:500;position:relative}
.sidebar li .ico{width:11px;height:11px;border:1.6px solid var(--white);border-radius:2px;margin-right:14px}
.sidebar li .more{position:absolute;left:193px;width:11px;height:11px;border-radius:50%;background:var(--white);color:var(--sidebar);font-size:10px;line-height:11px;text-align:center;font-weight:500}
.panel{position:absolute;left:241px;top:109px;width:939px;height:507px;background:var(--white);border:1px solid #e6e6e6}
.panel-bar{height:46px;background:var(--accent);display:flex;justify-content:flex-end;align-items:center;gap:5px;padding-right:10px}
.range-btn{height:30px;border:1px solid rgba(255,255,255,.8);color:var(--white);font-size:10.5px;font-weight:500;display:flex;align-items:center;gap:5px;padding:0 7px}
.range-btn i{width:8px;height:8px;border:1.4px solid var(--white);border-radius:50%}
.chart{position:absolute;left:0;top:0}
.footer{position:absolute;left:217px;right:0;top:1109px;height:51px;background:var(--sidebar);color:var(--white);font-size:11px;text-align:center;line-height:51px}
.footer .ver{position:absolute;right:21px;bottom:0;line-height:28px}
</style>
</head>
<body>
<div class="brand"><span class="brand-mark"></span><span class="brand-name">Estavo</span></div>

<header class="topbar">
  <div class="page-title">
    <svg width="17" height="15" viewBox="0 0 17 15"><path d="M8.5 1 1 7.5h2V14h4V10h3v4h4V7.5h2z" fill="#555"/></svg>
    Active Dashboard
  </div>
  <div class="stat-sep" style="left:347px"></div>
  <div class="stat" style="left:357px;width:84px">Properties<b>03</b></div>
  <div class="stat-sep" style="left:442px"></div>
  <div class="stat" style="left:452px;width:72px">Tenants<b>08</b></div>
  <div class="stat-sep" style="left:525px"></div>
  <div class="stat" style="left:530px;width:160px">Total Properties Area<b>422,000.00 sq.ft</b></div>
  <div class="stat-sep" style="left:690px"></div>
  <div class="stat" style="left:695px;width:134px">Rented Area<b>233,500.00 sq.ft</b></div>
  <div class="stat-sep" style="left:829px"></div>
  <div class="stat" style="left:837px;width:140px">Vacancies Area<b>188,500.00sq.ft</b></div>
</header>

<ul class="sidebar">
  <li><span class="ico"></span>Dashboard</li>
  <li><span class="ico"></span>Customers</li>
  <li><span class="ico"></span>Properties</li>
  <li><span class="ico"></span>Tenants</li>
  <li><span class="ico"></span>Contacts</li>
  <li><span class="ico"></span>Contractors</li>
  <li><span class="ico"></span>Employees</li>
  <li><span class="ico"></span>Compliance Management</li>
  <li><span class="ico"></span>Prevent.Maintenance<span class="more">+</span></li>
  <li><span class="ico"></span>Work Orders<span class="more">+</span></li>
  <li><span class="ico"></span>Purchase Orders</li>
  <li><span class="ico"></span>Property Inspections<span class="more">+</span></li>
  <li><span class="ico"></span>Energy Management</li>
  <li><span class="ico"></span>Risk Management</li>
  <li><span class="ico"></span>Project Management</li>
  <li><span class="ico"></span>Financial - Budgeting</li>
  <li><span class="ico"></span>Tenant Requests</li>
  <li><span class="ico"></span>Reports<span class="more">+</span></li>
  <li><span class="ico"></span>Visual Reports</li>
  <li><span class="ico"></span>Files</li>
  <li><span class="ico"></span>Pages<span class="more">+</span></li>
  <li><span class="ico"></span>Configurations<span class="more">+</span></li>
  <li><span class="ico"></span>Settings<span class="more">+</span></li>
</ul>

<section class="panel">
  <div class="panel-bar">
    <span class="range-btn"><i></i>Last 7 Days</span>
    <span class="range-btn"><i></i>Last months</span>
    <span class="range-btn"><i></i>Last 3 months</span>
    <span class="range-btn"><i></i>Next 7 Days</span>
    <span class="range-btn"><i></i>Next months</span>
    <span class="range-btn"><i></i>Next 3 months</span>
  </div>
  <svg class="chart" width="939" height="507" viewBox="0 0 939 507" font-family="Roboto, sans-serif">
    <g fill="none" stroke-width="1">
      <rect x="29" y="88" width="4" height="9" stroke="var(--accent)"/>
      <rect x="37" y="84" width="4" height="13" stroke="var(--accent)"/>
      <rect x="45" y="73" width="4" height="24" stroke="#333"/>
    </g>
    <text x="59" y="92" font-size="13" fill="#444">12/27/2020 - 01/03/2021</text>

    <g stroke="#666" stroke-width="1.3"><path d="M70 149h10M70 153h10M70 157h10"/></g>

    <g stroke="var(--grid)">
      <path d="M117.5 153H902M117.5 201H902M117.5 249H902M117.5 297H902M117.5 344H902"/>
    </g>
    <path d="M117.5 392H902" stroke="#bbb"/>
    <g stroke="#bbb"><path d="M117.5 392v7M216 392v7M314 392v7M412 392v7M510 392v7M608 392v7M706 392v7M804 392v7M902 392v7"/></g>

    <g font-size="8.5" fill="#555" text-anchor="end">
      <text x="111" y="156">1.25</text><text x="111" y="204">1</text>
      <text x="111" y="252">0.75</text><text x="111" y="300">0.5</text>
      <text x="111" y="347">0.25</text><text x="111" y="395">0</text>
    </g>
    <text transform="translate(52 276) rotate(-90)" font-size="12" fill="#666" text-anchor="middle">Number</text>

    <rect x="419" y="201" width="15" height="191" fill="var(--accent)"/>

    <g font-size="8.5" fill="#555" text-anchor="middle">
      <text x="164" y="410">12/27/2020</text><text x="263" y="410">12/28/2020</text>
      <text x="361" y="410">12/29/2020</text><text x="459" y="410">12/30/2020</text>
      <text x="558" y="410">12/31/2020</text><text x="656" y="410">01/01/2021</text>
      <text x="754" y="410">01/02/2021</text><text x="853" y="410">01/03/2021</text>
    </g>

    <g font-size="9" fill="#555">
      <rect x="118" y="444" width="13" height="12" fill="#4f6078"/>
      <text x="138" y="453">Scheduled</text><text x="138" y="466">Maintenance</text>
      <rect x="233" y="444" width="13" height="12" fill="#f28a1e"/>
      <text x="253" y="453">Completed</text><text x="253" y="466">Scheduled</text><text x="253" y="479">Maintenance</text>
      <rect x="348" y="444" width="13" height="12" fill="#1fa34a"/>
      <text x="368" y="453">Future Scheduled</text><text x="368" y="466">Maintenance</text>
      <rect x="463" y="444" width="13" height="12" fill="var(--accent)"/>
      <text x="483" y="453">Scheduled Work</text><text x="483" y="466">Orders</text>
      <rect x="577" y="444" width="13" height="12" fill="#6c3aa0"/>
      <text x="597" y="453">Completed work</text><text x="597" y="466">Orders</text>
      <rect x="692" y="444" width="13" height="12" fill="#e0148a"/>
      <text x="712" y="453">Property Inspections</text><text x="712" y="466">in Progress</text>
      <rect x="807" y="444" width="13" height="12" fill="#e8cf22"/>
      <text x="827" y="453">Completed Property</text><text x="827" y="466">Inspections</text>
    </g>
  </svg>
</section>

<footer class="footer">© Copyrights 2021- Estavo. All Rights Reserved.<span class="ver">C2</span></footer>
</body>
</html>
```